Modern Business Card for Larkwell 2018

Our company assumes the best about people. We are creating an online community of entrepreneurs and business leaders who struggle with marketing their business online.

This business card should POP! We recently got a new logo and are launching a new website next month, so our business cards should make a statement that feels:
-Fresh
-Smart
-Trustworthy
-Fun

Target Market(s)

small business owners, entrepreneurs

Industry/Entity Type

Digital Marketing

Contact Information for Business Card

Dimensions: 3.5" x 2"

Font styles to use
Sans Serif

Colors
f37122
ffffff

Requirements
Must have
• We need a business card with a modern, bold design. We will use one side of the card as a lead-generation offer, so text on one side will need to fit up to 140 characters. The business card should stick to our core colors (orange, black, and white).
Nice to have
• We think a vertical "portrait" design could be interesting.
Should not have
• Should not look like a traditional business card. The round icon should stand out from a distance.

```html
<!DOCTYPE html>
<html lang="en">
<head>
<meta charset="utf-8">
<title>Larkwell Business Card</title>
<link rel="stylesheet" href="https://fonts.googleapis.com/css2?family=Roboto:wght@400;500;700&family=Allura&display=swap">
<style>
  :root {
    --orange: #e8611f;
    --black: #1b1b1c;
    --white: #ffffff;
    --card-white: #f3f3f3;
    --backdrop: #dcdcdc;
    --rule: #2a2a2a;
    --muted: #3a3a3a;
  }
  * { box-sizing: border-box; margin: 0; padding: 0; }
  html, body { width: 1200px; height: 960px; overflow: hidden; }
  body {
    position: relative;
    background: var(--backdrop);
    font-family: "Roboto", Arial, sans-serif;
  }
  .card {
    position: absolute;
    width: 600px;
    height: 342px;
    overflow: hidden;
    box-shadow: 0 6px 18px rgba(0,0,0,0.18);
  }

  /* Front */
  .card-front { left: 302px; top: 118px; background: var(--card-white); }
  .band { position: absolute; top: 81px; height: 38px; }
  .band-black { left: 0; width: 260px; background: var(--black); }
  .band-orange { right: 0; width: 258px; background: var(--orange); }
  .brand-front {
    position: absolute; left: 260px; top: 78px; width: 82px; height: 44px;
    display: flex; align-items: center; justify-content: center; gap: 4px;
  }
  .brand-dot { border-radius: 50%; background: var(--orange); flex: none; }
  .brand-front .brand-dot { width: 12px; height: 12px; }
  .brand-front .brand-name {
    font-weight: 700; font-size: 11px; letter-spacing: 0.5px; color: var(--black);
  }
  .person-name {
    position: absolute; left: 0; right: 0; top: 168px;
    text-align: center;
    font-family: "Allura", cursive;
    font-weight: 400;
    font-size: 72px; line-height: 1; color: var(--orange);
  }
  .person-role {
    position: absolute; left: 0; right: 0; top: 244px;
    text-align: center; font-weight: 700; font-size: 20px; color: var(--black);
  }
  .person-email {
    position: absolute; left: 0; right: 0; top: 266px;
    text-align: center; font-size: 15px; color: var(--muted);
  }

  /* Back */
  .card-back { left: 299px; top: 499px; background: var(--orange); }
  .panel-dark {
    position: absolute; left: 0; top: 0; width: 299px; height: 100%; background: var(--black);
  }
  .brand-back {
    position: absolute; left: 0; width: 299px; top: 104px;
    display: flex; align-items: center; justify-content: center; gap: 12px;
  }
  .brand-back .brand-dot { width: 28px; height: 28px; }
  .brand-back .brand-name {
    font-weight: 700; font-size: 34px; letter-spacing: 1px; color: var(--white); line-height: 1;
  }
  .offer {
    position: absolute; left: 323px; top: 29px; width: 260px; color: var(--white);
  }
  .offer-headline {
    font-weight: 700; font-size: 18.5px; line-height: 21px; text-transform: uppercase;
  }
  .offer-body { margin-top: 6px; font-size: 15px; line-height: 19px; }
  .offer-url { margin-top: 9px; font-weight: 700; font-size: 19px; }
  .notes {
    position: absolute; left: 20px; top: 217px; width: 557px; height: 101px;
    background: var(--card-white); border-radius: 18px;
  }
  .notes-line {
    position: absolute; left: 24px; right: 28px; height: 1px; background: var(--rule);
  }
  .notes-line:nth-child(1) { top: 31px; }
  .notes-line:nth-child(2) { top: 71px; }
</style>
</head>
<body>
  <section class="card card-front" aria-label="Card front">
    <div class="band band-black"></div>
    <div class="band band-orange"></div>
    <div class="brand-front">
      <span class="brand-dot"></span>
      <span class="brand-name">Larkwell</span>
    </div>
    <h1 class="person-name">Dana Whitfield</h1>
    <p class="person-role">STORY MARKETING COACH</p>
    <p class="person-email">dana@larkwellnow.com</p>
  </section>

  <section class="card card-back" aria-label="Card back">
    <div class="panel-dark"></div>
    <div class="brand-back">
      <span class="brand-dot"></span>
      <span class="brand-name">LARKWELL</span>
    </div>
    <div class="offer">
      <p class="offer-headline">Reach more people.<br>Make more money.<br>Create more impact.</p>
      <p class="offer-body">Get your free Larkwell<br>Starter Package and our<br>marketing guide today at</p>
      <p class="offer-url">Larkwellnow.com/start</p>
    </div>
    <div class="notes">
      <div class="notes-line"></div>
      <div class="notes-line"></div>
    </div>
  </section>
</body>
</html>
```